Business Card for Field Lotus-Eco Friendly Organic Clothing Brand

We are looking for an amazing business card for our eco friendly, organic clothing brand. We are thinking maybe a business card with a peel off sticker on the back, since our hanging clothing tag is a peel off sticker on the back. I will attach our hang tag so we can make sure we stay in line with our design. I've also attached a bag we are doing because I do like the scattered emblem look as well.

```html
<!DOCTYPE html>
<html lang="en">
<head>
<meta charset="utf-8">
<title>Field Lotus Business Card</title>
<link href="https://fonts.googleapis.com/css2?family=Roboto:wght@400;500;700&family=Playfair+Display:wght@500&display=swap" rel="stylesheet">
<style>
  :root {
    --bg: #e9e6e1;
    --card-white: #ffffff;
    --forest: #0f6b35;
    --magenta: #d8127c;
    --silver: #b9b9b9;
    --silver-dark: #9c9c9c;
    --gold: #d8c690;
    --ink: #1a1a1a;
  }
  * { margin: 0; padding: 0; box-sizing: border-box; }
  html, body { width: 1200px; height: 902px; overflow: hidden; }
  body {
    background: var(--bg);
    font-family: "Roboto", Arial, sans-serif;
    position: relative;
  }
  .card {
    position: absolute;
    left: 240px;
    width: 720px;
    height: 411px;
    overflow: hidden;
    box-shadow: 0 6px 18px rgba(0,0,0,0.18);
  }
  .card--back { top: 25px; }
  .card--front { top: 466px; background: var(--card-white); }

  /* back */
  .back-pattern {
    position: absolute; inset: 0;
    background: radial-gradient(circle at 40% 45%, var(--silver) 0%, var(--silver-dark) 100%),
                linear-gradient(135deg, var(--gold), var(--silver));
    background-blend-mode: multiply;
  }
  .back-brand {
    position: absolute; left: 0; right: 0; top: 170px;
    text-align: center;
    font-weight: 700; font-size: 64px; color: var(--ink);
    letter-spacing: 1px;
  }

  /* front */
  .bands { position: absolute; inset: 0; }
  .front-brand {
    position: absolute; left: 250px; top: 88px;
    display: flex; align-items: center; gap: 16px;
  }
  .front-brand .dot {
    width: 22px; height: 22px; border-radius: 50%;
    background: var(--forest);
  }
  .front-brand .name {
    font-weight: 700; font-size: 60px; color: var(--magenta);
    letter-spacing: 1px;
  }
  .contact {
    position: absolute; right: 28px; top: 240px;
    list-style: none; text-align: right;
    color: #ffffff; font-size: 19px; line-height: 35px;
  }
  .contact li { display: flex; justify-content: flex-end; align-items: center; gap: 12px; }
  .contact svg { width: 18px; height: 18px; flex: none; }
  .person {
    position: absolute; left: 32px; top: 322px; color: #ffffff;
  }
  .person .full-name {
    font-family: "Playfair Display", Georgia, serif;
    font-weight: 500; font-size: 36px; line-height: 40px;
  }
  .person .role { font-weight: 500; font-size: 22px; line-height: 28px; }
</style>
</head>
<body>

<section class="card card--back">
  <div class="back-pattern" role="img" aria-label="Scattered gold words and peace signs on a silver background"></div>
  <div class="back-brand">Field Lotus</div>
</section>

<section class="card card--front">
  <svg class="bands" viewBox="0 0 720 411" width="720" height="411" aria-hidden="true">
    <polygon points="330,225 720,225 720,411 470,411" fill="var(--forest)"/>
    <polygon points="0,300 386,300 470,411 0,411" fill="var(--magenta)"/>
  </svg>

  <div class="front-brand">
    <span class="dot"></span>
    <span class="name">Field Lotus</span>
  </div>

  <ul class="contact">
    <li>(555) 014-2290
      <svg viewBox="0 0 18 18"><rect width="18" height="18" rx="2" fill="#fff"/><path d="M5 4l2.5 0 1 3-1.5 1a7 7 0 0 0 3 3l1-1.5 3 1v2.5c-5 0.5-9.5-4-9-9z" fill="var(--forest)"/></svg>
    </li>
    <li>www.fieldlotus.com
      <svg viewBox="0 0 18 18"><rect width="18" height="18" rx="2" fill="#fff"/><circle cx="9" cy="9" r="5.5" fill="none" stroke="var(--forest)" stroke-width="1.4"/><path d="M3.5 9h11M9 3.5c-3 3-3 8 0 11M9 3.5c3 3 3 8 0 11" fill="none" stroke="var(--forest)" stroke-width="1.2"/></svg>
    </li>
    <li>hello@fieldlotus.com
      <svg viewBox="0 0 18 18"><rect width="18" height="18" rx="2" fill="#fff"/><rect x="3" y="5" width="12" height="8" fill="none" stroke="var(--forest)" stroke-width="1.4"/><path d="M3 5l6 5 6-5" fill="none" stroke="var(--forest)" stroke-width="1.4"/></svg>
    </li>
    <li>Palm Cove, FL 33999
      <svg viewBox="0 0 18 18"><rect width="18" height="18" rx="2" fill="#fff"/><path d="M9 15s-4.5-4.5-4.5-7.5a4.5 4.5 0 0 1 9 0C13.5 10.5 9 15 9 15z" fill="var(--forest)"/><circle cx="9" cy="7.5" r="1.6" fill="#fff"/></svg>
    </li>
  </ul>

  <div class="person">
    <p class="full-name">Dana Marlowe</p>
    <p class="role">Managing Director</p>
  </div>
</section>

</body>
</html>
```